Vortaleen - Lead the Way!

Vortaleen is a new Silicon Valley company, of the pimrela founders from Berlin, which provides a "Shared Hive Circle". This platform allows the crowd to support startups with money, experts and fame. Our Vision is, that everyone should become an entrepreneur.

Pls find all brief details in the attached document
Updates

Would be nice to have a list of more social services I'm available on, like a list of pictograms of all my services:

Find me on: chattro, fennwix+, qrt, mivrel, datebloom, pohk, rplex, etc...

pls make sure to use the right font:
http://www.typelarder-demo.com/fonts/Orbitron

Target Market(s)

Main target market is those already involved in the startup industry, by fundraising, investing, advising, cofounding and working. Vortaleen brings a totaly new transparency and collaborative way of starting companies to that business.

· Entrepreneurs (looking for funding, team and community)
· Investors (looking for hot investments and )
· Experts (workers looking for startups they can work for equity)
· Incubators & Business Schools (looking for tools to advise startups)

Industry/Entity Type

It Company

Requirements
Must have
• Pls find all brief details in the attached document
Nice to have

```html
<!DOCTYPE html>
<html lang="en">
<head>
<meta charset="utf-8">
<title>Vortaleen – Business Card</title>
<link rel="stylesheet" href="https://fonts.googleapis.com/css2?family=Orbitron:wght@400;500;700&family=Open+Sans:wght@400&display=swap">
<style>
  :root {
    --backdrop: #38332f;
    --card-white: #ffffff;
    --brand-orange: #e35e3a;
    --text-grey: #6d6a69;
    --label-grey: #8a8583;
    --soft-white: #fbe3da;
    --icon-blue: #5a8fc0;
  }
  * { margin: 0; padding: 0; box-sizing: border-box; }
  html, body {
    width: 834px; height: 1200px; overflow: hidden;
    background: var(--backdrop);
  }
  .sheet { position: relative; width: 834px; height: 1200px; }

  .card { position: absolute; left: 97px; width: 640px; height: 370px; }
  .card--front { top: 157px; background: var(--card-white); }
  .card--back { top: 660px; background: var(--brand-orange); }

  .side-label {
    position: absolute; width: 834px; left: 0; text-align: center;
    font-family: Arial, Helvetica, sans-serif; font-size: 20px;
    color: var(--label-grey);
  }
  .side-label--front { top: 564px; }
  .side-label--back { top: 1067px; }

  /* front */
  .wordmark {
    position: absolute; left: 76px; top: 188px;
    font-family: "Orbitron", sans-serif; font-weight: 500; font-size: 27px;
    color: var(--brand-orange); display: flex; align-items: center; gap: 8px;
  }
  .wordmark__dot {
    width: 12px; height: 12px; border-radius: 50%; background: var(--brand-orange);
  }
  .tagline {
    position: absolute; left: 100px; top: 225px;
    font-family: "Open Sans", sans-serif; font-size: 13px; color: var(--text-grey);
  }
  .person { position: absolute; left: 303px; top: 153px; }
  .person__name {
    font-family: "Orbitron", sans-serif; font-weight: 500; font-size: 24px;
    letter-spacing: 0.5px; color: var(--brand-orange);
  }
  .person__role {
    margin-top: 6px;
    font-family: "Orbitron", sans-serif; font-weight: 500; font-size: 16px;
    letter-spacing: 0.5px; color: var(--text-grey);
  }
  .contact {
    position: absolute; left: 0; width: 630px; top: 306px; text-align: center;
    font-family: "Orbitron", sans-serif; font-size: 10px; color: var(--text-grey);
  }
  .contact__sep { color: var(--brand-orange); }
  .social {
    position: absolute; left: 72px; top: 326px; display: flex; gap: 14px;
    font-family: "Orbitron", sans-serif; font-size: 10px; color: var(--text-grey);
  }
  .social__item { display: flex; align-items: center; gap: 8px; }
  .social__mark { width: 9px; height: 9px; background: var(--icon-blue); }

  /* back */
  .invite {
    position: absolute; left: 0; width: 640px; top: 120px; text-align: center;
    color: var(--card-white); font-family: "Orbitron", sans-serif;
  }
  .invite__question { font-weight: 700; font-size: 17px; letter-spacing: 0.4px; }
  .invite__join { font-size: 13px; color: var(--soft-white); margin-top: 2px; }
  .divider { position: absolute; left: 118px; top: 284px; }
  .offices {
    position: absolute; left: 0; width: 640px; top: 306px; text-align: center;
    font-family: "Orbitron", sans-serif; font-size: 10.5px; line-height: 14px;
    color: var(--soft-white);
  }
</style>
</head>
<body>
<main class="sheet">
  <section class="card card--front">
    <div class="wordmark"><span>Vortaleen</span><span class="wordmark__dot"></span></div>
    <p class="tagline">Lead the Way!</p>

    <div class="person">
      <h1 class="person__name">LUKAS BRENNER</h1>
      <p class="person__role">FOUNDER AND CEO</p>
    </div>

    <p class="contact">044 210 387 516 <span class="contact__sep">|</span> www.vortaleen.com <span class="contact__sep">|</span> lb@vortaleen.com</p>
    <ul class="social">
      <li class="social__item"><span class="social__mark"></span>chirpa.com/lukasbrenner</li>
      <li class="social__item"><span class="social__mark"></span>facelog.com/lukasbrenner</li>
      <li class="social__item"><span class="social__mark"></span>linkwork.com/in/lukasbrenner</li>
    </ul>
  </section>
  <p class="side-label side-label--front">FRONT</p>

  <section class="card card--back">
    <div class="invite">
      <p class="invite__question">Are you interested in Startups, Investments, Work?</p>
      <p class="invite__join">Join: Facelog.com/Vortaleen</p>
    </div>
    <svg class="divider" width="400" height="2" viewBox="0 0 400 2" aria-hidden="true">
      <line x1="0" y1="1" x2="400" y2="1" stroke="#fbe3da" stroke-width="1" stroke-dasharray="5 4"/>
    </svg>
    <address class="offices" style="font-style:normal">
      Berlin - Lindenhof Strasse 14 . 10117 Berlin . Germany<br>
      Silicon Valley - 218 Orchard Ave . Sunnyvale . CA 94086
    </address>
  </section>
  <p class="side-label side-label--back">BACK</p>
</main>
</body>
</html>
```